Harrow Grading LLC business card design

Excavation company business cards

Contact Information for Business Card

Harrow Grading LLC cell phone 208-417-6290 office phone 208-319-4856 harrowgradingllc@maplecove.com Driveways, site prep, retaining walls, septic systems, rock delivery

Colors

Designer to choose colors to be used in the design.

```html
<!DOCTYPE html>
<html lang="en">
<head>
<meta charset="utf-8">
<title>Harrow Grading LLC – Business Card</title>
<link rel="stylesheet" href="https://fonts.googleapis.com/css2?family=Montserrat:wght@500;700;800&family=Roboto:wght@400;500&display=swap">
<style>
  :root{
    --card-white:#ffffff;
    --card-dark:#1c1c1c;
    --orange:#ec6f25;
    --grey-band:#5f5f5f;
    --ink:#1d1d1d;
    --rule:#8a8a8a;
    --light:#f2f2f2;
  }
  *{box-sizing:border-box;margin:0;padding:0}
  html,body{width:1200px;height:788px;overflow:hidden}
  body{
    background:linear-gradient(160deg,#d2d2d2,#a9a9a9);
    font-family:"Montserrat",sans-serif;
    position:relative;
  }
  .card{
    position:absolute;
    width:520px;height:297px;
    border-radius:22px;
    overflow:hidden;
    box-shadow:0 14px 30px rgba(0,0,0,.28);
  }
  .card--front{left:44px;top:245px;background:var(--card-white)}
  .card--back{left:636px;top:245px;background:var(--card-dark)}

  .front-bands{position:absolute;inset:0}

  .brand{
    position:absolute;left:130px;top:86px;
    display:flex;align-items:center;gap:10px;
  }
  .brand__mark{width:14px;height:14px;background:var(--orange);flex:none}
  .brand__name{
    font-weight:800;font-size:22px;color:var(--orange);
    letter-spacing:.5px;line-height:1.05;text-transform:uppercase;white-space:nowrap;
  }

  .person{position:absolute;left:60px;top:192px}
  .person__name{font-weight:700;font-size:22px;color:var(--orange);letter-spacing:.3px;text-transform:uppercase;white-space:nowrap}
  .person__role{font-family:"Roboto",sans-serif;font-size:15px;color:var(--ink);margin-top:2px;padding-left:70px}

  .divider{position:absolute;left:292px;top:146px;width:1px;height:74px;background:var(--rule)}

  .contacts{position:absolute;left:306px;top:142px;list-style:none;font-family:"Roboto",sans-serif;font-size:11.5px;color:var(--ink)}
  .contacts li{display:flex;align-items:center;gap:6px;line-height:20px;white-space:nowrap}
  .contacts svg{width:10px;height:10px;flex:none}

  .pattern{position:absolute;inset:0;background:linear-gradient(135deg,#2a2a2a 0%,#1c1c1c 55%,#141414 100%)}
  .back-brand{
    position:absolute;left:0;right:0;top:98px;
    display:flex;justify-content:center;align-items:center;gap:10px;
  }
  .back-brand .brand__name{font-size:24px}

  .services{
    position:absolute;left:60px;right:40px;bottom:52px;
    display:grid;grid-template-columns:1fr 1.4fr 1.2fr;row-gap:6px;
    list-style:none;color:var(--light);font-size:15px;font-weight:500;
  }
  .services li{display:flex;align-items:center;gap:7px;white-space:nowrap}
  .services li::before{content:"";width:5px;height:5px;border-radius:50%;background:var(--orange)}
</style>
</head>
<body>

<section class="card card--front" aria-label="Business card front">
  <svg class="front-bands" viewBox="0 0 520 297" preserveAspectRatio="none" aria-hidden="true">
    <polygon points="0,0 225,0 205,66 0,58" fill="var(--orange)"/>
    <polygon points="225,0 520,0 520,34 205,66" fill="var(--grey-band)"/>
  </svg>

  <div class="brand">
    <span class="brand__mark"></span>
    <span class="brand__name">Harrow Grading LLC</span>
  </div>

  <div class="person">
    <p class="person__name">Dale Warner</p>
    <p class="person__role">Founder</p>
  </div>

  <span class="divider"></span>

  <ul class="contacts">
    <li><svg viewBox="0 0 10 10"><path d="M2 1l2 2-1 1.3c.6 1.2 1.5 2.1 2.7 2.7L7 6l2 2-1.2 1.2C4.5 9 1 5.5.8 2.2z" fill="var(--orange)"/></svg>208-319-4856</li>
    <li><svg viewBox="0 0 10 10"><rect x="2.5" y=".5" width="5" height="9" rx="1" fill="none" stroke="var(--orange)"/></svg>208-417-6290</li>
    <li><svg viewBox="0 0 10 10"><rect x=".5" y="2" width="9" height="6" fill="var(--orange)"/><path d="M.5 2l4.5 3.5L9.5 2" fill="none" stroke="#fff" stroke-width=".8"/></svg>harrowgradingllc@maplecove.com</li>
    <li><svg viewBox="0 0 10 10"><circle cx="5" cy="5" r="4.5" fill="var(--orange)"/><path d="M.5 5h9M5 .5c2 2 2 7 0 9M5 .5c-2 2-2 7 0 9" fill="none" stroke="#fff" stroke-width=".6"/></svg>www.harrowgradingllc.net</li>
  </ul>
</section>

<section class="card card--back" aria-label="Business card back">
  <div class="pattern" role="img" aria-label="Faint repeating pattern of excavators and mountain peaks"></div>

  <div class="back-brand">
    <span class="brand__mark"></span>
    <span class="brand__name">Harrow Grading LLC</span>
  </div>

  <ul class="services">
    <li>Driveways</li>
    <li>Retaining Walls</li>
    <li>Rock Delivery</li>
    <li>Site Prep</li>
    <li>Septic Systems</li>
  </ul>
</section>

</body>
</html>
```